Salon and Spa Distributor Business Card

Need a business card. We are are distributor in the salon and spa industry. We identify with natural beauty. Need a card with:
Company Name: Petal Quarry"
Title: "President & CEO"
Address
Company Phone number
email
website
Tag Line:" Naturally Sourced For Salons"

Industry/Entity Type

Business

Contact Information for Business Card

Name: Dov Strommen
Title: "President & CEO"
Address: 31 Harlow Ln, Bexmoor, NJ 07813
Company Phone number: 800-463-5918
email: dovstrommen@petalquarry.example
website: www.petalquarry.example

Requirements
Should not have
• No black backgrounds

```html
<!DOCTYPE html>
<html lang="en">
<head>
<meta charset="utf-8">
<title>Petal Quarry Business Card</title>
<link rel="stylesheet" href="https://fonts.googleapis.com/css2?family=Questrial&display=swap">
<style>
  :root {
    --leaf: #4cae3c;
    --leaf-deep: #1f8a3a;
    --leaf-light: #6cc04a;
    --ink: #2b2b2b;
    --card: #ffffff;
    --backdrop: #e9ebe8;
  }
  * { margin: 0; padding: 0; box-sizing: border-box; }
  html, body {
    width: 1200px; height: 880px; overflow: hidden;
    background: var(--backdrop);
    font-family: "Questrial", "Century Gothic", sans-serif;
    color: var(--ink);
  }
  .canvas { position: relative; width: 1200px; height: 880px; }
  .card {
    position: absolute; width: 560px; height: 320px;
    background: var(--card); border-radius: 22px;
    box-shadow: 0 10px 30px rgba(0,0,0,.12);
    overflow: hidden;
  }
  .card-front { left: 80px; top: 90px; }
  .card-back { left: 560px; top: 470px; }

  .front-brand {
    position: absolute; left: 0; right: 0; top: 110px;
    display: flex; align-items: center; justify-content: center; gap: 18px;
  }
  .brand-dot {
    width: 64px; height: 64px; border-radius: 50%;
    background: linear-gradient(135deg, var(--leaf-light), var(--leaf-deep));
  }
  .brand-name { color: var(--leaf); font-size: 46px; font-weight: 400; }
  .front-tagline {
    position: absolute; left: 0; right: 0; top: 218px; text-align: center;
    font-size: 15px; letter-spacing: 4px;
  }

  .back-accent {
    position: absolute; left: -190px; bottom: -190px;
    width: 410px; height: 410px; border-radius: 50%;
    background: linear-gradient(135deg, var(--leaf-light), var(--leaf-deep));
  }
  .back-info { position: absolute; right: 24px; top: 28px; width: 292px; }
  .back-name { color: var(--leaf); font-size: 36px; line-height: 1; }
  .back-tagline { font-size: 14px; margin-top: 4px; }
  .person { margin-top: 24px; }
  .person-name { color: var(--leaf); font-size: 20px; }
  .person-title { font-size: 14px; }
  .address { margin-top: 14px; font-size: 14px; line-height: 1.35; }
  .contacts { list-style: none; margin-top: 10px; font-size: 14px; }
  .contacts li { display: flex; align-items: center; gap: 8px; line-height: 1.55; white-space: nowrap; }
  .icon { width: 16px; height: 16px; flex: none; }
</style>
</head>
<body>
<div class="canvas">
  <section class="card card-front">
    <div class="front-brand">
      <span class="brand-dot"></span>
      <span class="brand-name">Petal Quarry</span>
    </div>
    <p class="front-tagline">Naturally Sourced For Salons</p>
  </section>

  <section class="card card-back">
    <div class="back-accent" role="img" aria-label="Green botanical illustration of leaves and flowing hair"></div>

    <div class="back-info">
      <div class="back-name">Petal Quarry</div>
      <div class="back-tagline">Naturally Sourced For Salons</div>
      <div class="person">
        <div class="person-name">Dov Strommen</div>
        <div class="person-title">President &amp; CEO</div>
      </div>
      <div class="address">31 Harlow Ln,<br>Bexmoor, NJ 07813</div>
      <ul class="contacts">
        <li>
          <svg class="icon" viewBox="0 0 16 16" aria-hidden="true"><rect width="16" height="16" rx="3" fill="#4cae3c"/><path d="M5 3.5l2 2-1 1.3c.6 1.3 1.6 2.3 2.9 2.9l1.3-1 2 2-1.2 1.8C7.8 12.2 3.8 8.2 3.5 4.7z" fill="#fff"/></svg>
          800-463-5918
        </li>
        <li>
          <svg class="icon" viewBox="0 0 16 16" aria-hidden="true"><rect width="16" height="16" rx="3" fill="#4cae3c"/><rect x="3" y="4.5" width="10" height="7" fill="none" stroke="#fff" stroke-width="1.2"/><path d="M3 4.5l5 4 5-4" fill="none" stroke="#fff" stroke-width="1.2"/></svg>
          dovstrommen@petalquarry.example
        </li>
        <li>
          <svg class="icon" viewBox="0 0 16 16" aria-hidden="true"><rect width="16" height="16" rx="3" fill="#4cae3c"/><circle cx="8" cy="8" r="4.8" fill="none" stroke="#fff" stroke-width="1.1"/><ellipse cx="8" cy="8" rx="2" ry="4.8" fill="none" stroke="#fff" stroke-width="1.1"/><path d="M3.2 8h9.6" stroke="#fff" stroke-width="1.1"/></svg>
          www.petalquarry.example
        </li>
      </ul>
    </div>
  </section>
</div>
</body>
</html>
```